Creative, fresh business card design for Ripplecraft Facades

We need a fresh, creative business card design for Ripplecraft Facades. We are the manufacturer of Ripplecraft Facades in Australia. Wall panels are 2400 x 1200mm panels made from MDF and feature 3D patterns on the face of the panel. The colours to be used are green, silver/grey and white RGB
Red 187
Green 207
Blue 65.

An idea is to possibly use a watermark of one of our designs as a background (like on the "Grids" design on the left hand side of page 2 of our brochure).

Target Market(s)

Interior designers, architects, builders and home renovators

Industry/Entity Type

Business

Contact Information for Business Card

Details to go on the card are:
Our logo (attached),
Slogan: "Decorative panels for interiors and exteriors",
Contact name,
Position,
Mobile phone number,
Business address,
Business phone,
Business fax,
Website and
Email address.

I have attached a few images of our panels and our brochure for reference.

The colours of the business card should feature our logo colours which are: RGB
Red 187
Green 207
Blue 65

Requirements
Must have
• Very modern fonts and design. Some of the designs shown especially the "Prisms" design which is a popular design.
Nice to have
• Creative but simple design. Very contemporary.
Should not have
• Anything ornate or old fashioned.

```html
<!DOCTYPE html>
<html lang="en">
<head>
<meta charset="utf-8">
<title>Ripplecraft Facades – Business Card</title>
<link rel="stylesheet" href="https://fonts.googleapis.com/css2?family=Arimo:wght@400;700&family=Questrial&display=swap">
<style>
  :root {
    --backdrop: #d8d4cd;
    --card: #efeeeb;
    --card-edge: #c9c7c2;
    --charcoal: #4a4a4b;
    --band: #58585a;
    --brand-green: #bbcf41;
    --deep-green: #7f9a33;
    --slogan: #4f4f50;
    --light-text: #ffffff;
    --soft-text: #f3f6e6;
  }
  * { margin: 0; padding: 0; box-sizing: border-box; }
  html, body {
    width: 1200px;
    height: 969px;
    overflow: hidden;
    background: var(--backdrop);
  }
  .canvas {
    position: relative;
    width: 1200px;
    height: 969px;
  }
  .card {
    position: absolute;
    left: 391px;
    top: 117px;
    width: 417px;
    height: 735px;
    background: var(--card);
    border: 1px solid var(--card-edge);
  }
  .top-bar {
    position: absolute;
    left: 36px;
    top: 3px;
    width: 342px;
    height: 57px;
    background: var(--charcoal);
  }
  .mark-block {
    position: absolute;
    left: 36px;
    top: 60px;
    width: 342px;
    height: 147px;
    background: linear-gradient(180deg, var(--brand-green), #a9c03c);
  }
  .name-band {
    position: absolute;
    left: 36px;
    top: 219px;
    width: 342px;
    height: 42px;
    background: var(--band);
    color: var(--light-text);
    font-family: "Questrial", sans-serif;
    font-size: 25px;
    line-height: 42px;
    text-align: center;
    letter-spacing: 0.3px;
  }
  .slogan {
    position: absolute;
    left: 26px;
    top: 262px;
    width: 362px;
    font-family: "Questrial", sans-serif;
    font-size: 20px;
    line-height: 31px;
    letter-spacing: 2.6px;
    color: var(--slogan);
    text-align: center;
    white-space: nowrap;
  }
  .contact-panel {
    position: absolute;
    left: 36px;
    top: 325px;
    width: 342px;
    height: 407px;
    background: linear-gradient(180deg, var(--deep-green) 0%, #9ab538 45%, var(--brand-green) 100%);
    font-family: "Arimo", sans-serif;
    color: var(--soft-text);
    text-align: center;
  }
  .person-name {
    position: absolute;
    top: 62px;
    width: 100%;
    font-size: 24px;
    font-weight: 700;
    letter-spacing: 0.5px;
    color: var(--light-text);
  }
  .person-role {
    position: absolute;
    top: 93px;
    width: 100%;
    font-size: 19px;
  }
  .contact-lines {
    position: absolute;
    top: 142px;
    width: 100%;
    list-style: none;
    font-size: 18px;
    line-height: 28.5px;
    white-space: nowrap;
  }
  .address {
    position: absolute;
    top: 298px;
    width: 100%;
    font-style: normal;
    font-size: 18px;
    line-height: 25px;
  }
</style>
</head>
<body>
<main class="canvas">
  <article class="card">
    <div class="top-bar"></div>
    <div class="mark-block"></div>
    <div class="name-band">Ripplecraft Facades</div>
    <p class="slogan">decorative panels for<br>interiors and exteriors</p>
    <section class="contact-panel">
      <h1 class="person-name">MARA ELLISON</h1>
      <p class="person-role">CEO&amp;Founder</p>
      <ul class="contact-lines">
        <li>Mob : 0412 583 906</li>
        <li>Tel : (03) 5214 7786</li>
        <li>Fax : (03) 5214 7790</li>
        <li>mellison@ripplecraftfacades.com</li>
        <li>www.ripplecraftfacades.com</li>
      </ul>
      <address class="address">42 Tidewater Street<br>Geelong, Victoria 3220</address>
    </section>
  </article>
</main>
</body>
</html>
```